VOR Exterior Coatings

double sided. the front i want the name of the business each word on a new line with the VOR being bigger. id like teal, black and white colors. the back i want my contact info. Flat, no gloss. Something professional and I want to feel the letters bump put of the card. if possible maybe a paint sprayer in corner. not a car paint spray. (no tank on top of gun)
no vehicle paint sprayers. that means no tank on top of the gun. doesn't have to have a sprayer. black/dark background on the front. white back ground on back with info

```html
<!DOCTYPE html>
<html lang="en">
<head>
<meta charset="utf-8">
<title>VOR Exterior Coatings – Business Card</title>
<link rel="stylesheet" href="https://fonts.googleapis.com/css2?family=Roboto:wght@400;700;900&display=swap">
<style>
  :root {
    --backdrop: #dfdfdf;
    --paper: #ffffff;
    --charcoal: #262828;
    --teal: #00857d;
    --ink: #1e1e1e;
    --rule: #a8a8a8;
    --silver: #dcdcdc;
  }
  * { margin: 0; padding: 0; box-sizing: border-box; }
  html, body {
    width: 1200px; height: 801px; overflow: hidden;
    background: var(--backdrop);
    font-family: "Roboto", sans-serif;
  }
  .card {
    position: absolute; top: 274px;
    width: 443px; height: 263px;
  }
  .card--info { left: 153px; background: var(--paper); }
  .card--brand { left: 625px; background: var(--charcoal); }

  .wordmark {
    position: absolute;
    font-family: "Roboto", sans-serif;
    font-weight: 900;
    text-transform: uppercase;
    line-height: 1;
  }
  .wordmark span { display: block; }
  .card--info .wordmark { left: 31px; top: 84px; width: 168px; color: var(--charcoal); }
  .card--info .wordmark__lead { font-size: 56px; letter-spacing: 9px; margin-bottom: 3px; }
  .card--info .wordmark__line { font-size: 24px; letter-spacing: 1.2px; }

  .card--brand .wordmark { left: 112px; top: 70px; width: 220px; color: var(--silver); }
  .card--brand .wordmark__lead { font-size: 74px; letter-spacing: 12px; margin-bottom: 4px; }
  .card--brand .wordmark__line { font-size: 31px; letter-spacing: 1.8px; }

  .divider {
    position: absolute; left: 220px; top: 70px;
    width: 2px; height: 123px; background: var(--rule);
  }
  .contact { position: absolute; left: 240px; top: 67px; color: var(--ink); }
  .contact__name {
    font-weight: 900; font-size: 17px; color: var(--teal);
    letter-spacing: 0.3px; line-height: 1;
  }
  .contact__title { font-size: 12.5px; margin-top: 3px; }
  .contact__list { list-style: none; margin-top: 10px; }
  .contact__list li {
    display: flex; align-items: center; gap: 4px;
    font-size: 12.5px; height: 16.5px;
  }
  .contact__list svg { width: 13px; height: 13px; fill: var(--teal); flex: none; }
  .accent { color: var(--teal); }
  .contact__address { font-size: 12.5px; line-height: 15.5px; margin-top: 9px; padding-left: 2px; }
</style>
</head>
<body>
  <section class="card card--info">
    <div class="wordmark">
      <span class="wordmark__lead">VOR</span>
      <span class="wordmark__line">Exterior</span>
      <span class="wordmark__line">Coatings</span>
    </div>
    <div class="divider"></div>
    <div class="contact">
      <p class="contact__name">MARCUS ELLERY</p>
      <p class="contact__title">Managing Director</p>
      <ul class="contact__list">
        <li>
          <svg viewBox="0 0 24 24" aria-hidden="true"><path d="M6.6 10.8a15 15 0 0 0 6.6 6.6l2.2-2.2c.3-.3.7-.4 1-.2 1.1.4 2.3.6 3.6.6.6 0 1 .4 1 1V20c0 .6-.4 1-1 1A17 17 0 0 1 3 4c0-.6.4-1 1-1h3.5c.6 0 1 .4 1 1 0 1.3.2 2.5.6 3.6.1.3 0 .7-.2 1z"/></svg>
          041-555 208 317
        </li>
        <li>
          <svg viewBox="0 0 24 24" aria-hidden="true"><path d="M2 5h20v14H2z M3.5 6.5v.4l8.5 6 8.5-6v-.4z"/></svg>
          hello@vorcoatings.com
        </li>
        <li>
          <svg viewBox="0 0 24 24" aria-hidden="true"><path d="M12 2a10 10 0 1 0 0 20 10 10 0 0 0 0-20zm6.9 9h-3c-.1-2.4-.6-4.5-1.4-6A8 8 0 0 1 18.9 11zM12 4c.9 1.2 1.7 3.6 1.9 7h-3.8C10.3 7.6 11.1 5.2 12 4zM9.5 5c-.8 1.5-1.3 3.6-1.4 6h-3A8 8 0 0 1 9.5 5zM5.1 13h3c.1 2.4.6 4.5 1.4 6A8 8 0 0 1 5.1 13zM12 20c-.9-1.2-1.7-3.6-1.9-7h3.8c-.2 3.4-1 5.8-1.9 7zm2.5-1c.8-1.5 1.3-3.6 1.4-6h3a8 8 0 0 1-4.4 6z"/></svg>
          www.<span class="accent">vorcoatings</span>.com
        </li>
      </ul>
      <p class="contact__address">18 Harbor Mill Road<br>Eastbrook, 30718</p>
    </div>
  </section>

  <section class="card card--brand">
    <div class="wordmark">
      <span class="wordmark__lead">VOR</span>
      <span class="wordmark__line">Exterior</span>
      <span class="wordmark__line">Coatings</span>
    </div>
  </section>
</body>
</html>
```